Vorelan.com Personal Trainer/Fitness Website

I want a website to market my personal training/Outdoor Bootcamp Class services, as well as to ditribute nutrivex. I need a logo as well I included an address for the Harbor Gales 1975 logo. I'd like Vorelan in place of Harbor Gales, and in Black and white, just different enough so I can't get sued by the PBL.
https://www.pictofind.example/imgres?imgurl=http%3A%2F%2Fwww.darnell-quibury.example%2Fwp-content%2Fuploads%2F2014%2F01%2Fgales_logo4.jpg&imgrefurl=http%3A%2F%2Fwww.darnell-quibury.example%2Fpbl-logo-redesigns-harbor-gales%2F&docid=_qkwzR7TBAgXpL&tbnid=m4tpU8KdOXjnRP%3A&w=600&h=450&client=ms-android-carrier&bih=512&biw=360&ved=0ahUKEwiRtpgyp9HMAhUTwGMKHRPMBWMQMwg6KBQwFA&iact=mrc&uact=8.
It should be about 5 pages 1. home 2. about 3. Services 4. Blog/Videos and programs 5. Contact.
http://www.dorvinfitness.example.uk/ is a website I like the style of.

Target Market(s)

Seattle area

Industry/Entity Type

Fitness

Coding

Coded - Design and coding required

Number of Pages Required

4 page

Font styles to use
Serif
Sans Serif

Requirements
Must have
• A minimal look
Nice to have
• A logo similar to the 1975 Harbor Galewinds Logo, with a Small Milo Brandt ripping his shirt open(with a picture of the logo on his shirt, picture within picture) to turn into Ironjaw in the center. Skyline is black, Background and small figure white(with black logo on shirt)

```html
<!DOCTYPE html>
<html lang="en">
<head>
<meta charset="utf-8">
<title>Vorelan – Personal Training</title>
<link href="https://fonts.googleapis.com/css2?family=Exo+2:wght@700&family=Lato:wght@400;700;900&display=swap" rel="stylesheet">
<style>
:root{
  --white:#ffffff;
  --black:#000000;
  --ink:#222222;
  --nav:#2b2b2b;
  --charcoal:#333333;
  --gallery:#3a3a3a;
  --footer:#2a2a2a;
  --field:#2f2f2f;
  --line:#8a8a8a;
  --muted:#bdbdbd;
  --bar:#4a4a4a;
}
*{box-sizing:border-box;margin:0;padding:0}
html,body{width:1200px;height:3462px;overflow:hidden}
body{font-family:"Lato",Arial,sans-serif;color:var(--ink);background:var(--white);position:relative}
.section{position:absolute;left:0;width:1200px;overflow:hidden}
.abs{position:absolute}
.center{text-align:center;left:0;width:1200px}

/* header */
.site-header{top:0;height:134px;background:var(--white)}
.brand{left:81px;top:14px;width:110px;text-align:center}
.brand-mark{display:block;width:62px;height:62px;border-radius:50%;background:var(--black);margin:0 auto 6px}
.brand-name{font-weight:900;font-size:26px;letter-spacing:1px;color:var(--black)}
.cta{left:905px;top:23px;width:214px;height:42px;background:var(--black);color:var(--white);font-weight:700;font-size:20px;line-height:42px;text-align:center;border-radius:3px}
.header-contact{left:855px;top:84px;display:flex;align-items:center;gap:10px;font-weight:700;font-size:21px;color:var(--ink)}
.icon-dot{width:30px;height:30px;border-radius:50%;background:var(--ink);display:inline-block}
.icon-dot.light{background:#9a9a9a}
.main-nav{top:134px;height:46px;background:var(--nav);display:flex;padding-left:81px}
.main-nav a{width:148px;height:46px;line-height:46px;text-align:center;color:var(--white);font-size:13px;font-weight:700;letter-spacing:1px;text-decoration:none;border-right:1px solid #444}
.main-nav a.active{background:var(--black)}

/* hero */
.hero{top:180px;height:621px;background:linear-gradient(100deg,#9a8f86 0%,#c9bdb2 30%,#6c5a4e 55%,#3c3430 80%,#7f7873 100%)}
.hero-caption{left:0;top:185px;width:485px;height:254px;background:rgba(20,20,20,.72);padding:48px 0 0 82px}
.hero-caption h1{font-family:"Exo 2",Arial,sans-serif;font-size:37px;line-height:55px;color:var(--white);text-transform:uppercase}
.dots{top:566px;display:flex;justify-content:center;gap:10px}
.dots span{width:14px;height:14px;border-radius:50%;background:rgba(255,255,255,.55)}
.dots span.on{background:var(--white)}

/* welcome */
.welcome{top:801px;height:222px;background:var(--white);overflow:visible}
.welcome-badge{left:568px;top:-32px;width:64px;height:64px;border-radius:50%;background:var(--black);border:4px solid var(--white)}
.welcome h2{top:38px;font-weight:400;font-size:27px;color:var(--ink)}
.welcome h2 b{font-weight:900}
.welcome p{left:81px;top:80px;width:1038px;text-align:center;font-size:14.5px;line-height:22px;color:#333}
.pill{display:inline-block;background:var(--ink);color:var(--white);font-size:11px;font-weight:900;border-radius:14px;padding:0 16px;height:26px;line-height:26px;letter-spacing:.5px}
.welcome .pill{position:absolute;left:547px;top:162px}

/* section titles */
.title{font-weight:400;font-size:28px;color:var(--white);letter-spacing:1px}
.title b{font-weight:900}
.rule{height:1px;background:var(--line)}
.kicker{font-size:15px;color:var(--white);letter-spacing:.5px}

/* services */
.services{top:1023px;height:440px;background:linear-gradient(90deg,#4b4b4b,#6b6b6b 45%,#505050)}
.services-cards{left:0;top:0;width:1200px;height:440px}
.service{position:absolute;top:210px;width:280px;margin-left:-140px;text-align:center;color:var(--white);font-size:13px;font-weight:900;letter-spacing:.3px}
.service i{display:block;width:116px;height:116px;margin:0 auto 40px;border-radius:50%;background:var(--black);border:4px solid var(--white)}

/* gallery */
.gallery{top:1463px;height:506px;background:var(--gallery)}
.tile{position:absolute}
.video-controls{left:0;bottom:0;width:309px;height:30px;background:rgba(0,0,0,.7)}
.arrow{position:absolute}

/* events */
.events{top:1969px;height:551px;background:linear-gradient(90deg,#5a5a5a,#7a7a7a 50%,#5c5c5c)}
.event{position:absolute;top:177px;width:327px;height:300px;background:var(--white);border-radius:3px;overflow:hidden;text-align:center}
.event-photo{height:173px}
.date{position:absolute;left:8px;top:0;width:42px;height:52px;background:var(--black);color:var(--white);text-align:center;padding-top:4px}
.date strong{display:block;font-size:19px;line-height:22px}
.date small{font-size:11px;font-weight:700}
.event h3{font-size:15px;font-weight:900;margin:14px 0 6px;color:var(--ink)}
.event p{font-size:13px;line-height:17px;padding:0 34px;color:#333}
.event .pill{margin-top:10px;height:24px;line-height:24px;font-size:10px}

/* testimonials */
.testimonials{top:2520px;height:434px;background:var(--black)}
.quote{left:166px;top:152px;width:868px;height:155px;background:var(--charcoal);border-radius:6px;padding:22px 60px 0 60px;color:#e6e6e6;font-size:14px;font-weight:700;line-height:22px;letter-spacing:.2px}
.quote-name{left:293px;top:340px;color:var(--white);font-weight:900;font-size:19px;letter-spacing:1px}

/* footer */
.footer{top:2954px;height:462px;background:var(--footer);color:var(--white)}
.newsletter{left:81px;top:53px;width:754px;height:70px;border:1px solid #555;border-radius:3px;display:flex;align-items:center;padding:0 14px;gap:14px}
.newsletter .label{font-weight:900;font-size:17px;letter-spacing:.5px;white-space:nowrap}
.newsletter .input{width:385px;height:40px;background:var(--white);color:#333;font-size:13px;line-height:40px;padding-left:10px}
.newsletter .btn{height:40px;line-height:40px;padding:0 12px;background:var(--black);font-size:13px;font-weight:700;margin-left:-14px}
.follow{left:889px;top:77px;display:flex;align-items:center;gap:12px;font-weight:900;font-size:17px}
.ftitle{font-weight:900;font-size:17px;letter-spacing:.5px;display:flex;align-items:center;gap:10px}
.field{position:absolute;height:40px;border:1px solid #666;background:var(--field);font-size:13px;padding:10px 12px;color:#ddd;border-radius:2px}
.submit{position:absolute;height:40px;background:var(--black);font-size:13px;font-weight:900;text-align:center;line-height:40px;letter-spacing:.5px}
.links{list-style:none;font-size:13px;line-height:29px;color:#ddd}
.links li::before{content:"›";margin-right:10px}
.vline{position:absolute;width:1px;background:#4a4a4a}
.copyright{top:3416px;height:46px;background:var(--bar);border-top:3px solid #777;color:#e0e0e0;font-size:12px;text-align:center;line-height:40px;letter-spacing:.5px;overflow:visible}
</style>
</head>
<body>

<header class="section site-header">
  <div class="abs brand"><span class="brand-mark"></span><span class="brand-name">VORELAN</span></div>
  <div class="abs cta">Join A Session</div>
  <div class="abs header-contact">
    <svg width="28" height="28" viewBox="0 0 28 28"><circle cx="14" cy="14" r="14" fill="#9a9a9a"/><path d="M9 7l4 4-2 2c1 2 3 4 5 5l2-2 4 4-2 3C13 22 6 15 6 9z" fill="#222"/></svg>
    <span>123-345-5678</span>
    <span class="icon-dot" style="background:#2c4a85"></span>
    <span class="icon-dot light"></span>
  </div>
</header>

<nav class="section main-nav">
  <a class="active">HOME</a><a>ABOUT</a><a>SERVICES</a><a>BLOG</a><a>VIDEOS</a><a>PROGRAMS</a><a>CONTACT</a>
</nav>

<section class="section hero" role="img" aria-label="Trainer coaching a client through sit-ups in a busy gym">
  <div class="abs hero-caption"><h1>Where personal<br>training meets<br>group training</h1></div>
  <div class="abs center dots"><span class="on"></span><span></span><span></span></div>
</section>

<section class="section welcome">
  <div class="abs welcome-badge"></div>
  <h2 class="abs center">WELCOME TO <b>VORELAN</b></h2>
  <p class="abs">Lorem ipsum dolor sit amet, consectetuer adipiscing elit, sed diam nonummy nibh euismod tincidunt ut laoreet dolore magna aliquam erat volutpat. Ut wisi enim ad minim veniam, quis nostrud exerci tation ullamcorper suscipit lobortis nisl ut aliquip ex ea commodo consequat. Duis autem vel eum iriure dolor in hendrerit in vulputate velit esse molestie consequat, vel illum dolore eu feugiat nulla facilisis.</p>
  <span class="pill">READ MORE</span>
</section>

<section class="section services">
  <div class="abs services-cards" role="img" aria-label="Group stretching class in a studio, darkened behind the section"></div>
  <h2 class="abs center title" style="top:62px">OUR <b>SERVICES</b></h2>
  <div class="abs rule" style="left:347px;top:124px;width:506px"></div>
  <div class="abs center kicker" style="top:148px">SELECT TO LEARN MORE!</div>
  <div class="service" style="left:185px"><i></i>PERSONAL TRAINING</div>
  <div class="service" style="left:459px"><i></i>OUTDOOR BOOTCAMP CLASSES</div>
  <div class="service" style="left:736px"><i></i>OUTDOOR GROUP TRAINING</div>
  <div class="service" style="left:1011px"><i></i>ONLINE COACHING</div>
</section>

<section class="section gallery">
  <h2 class="abs center title" style="top:48px">OUR <b>GALLERY</b></h2>
  <div class="abs rule" style="left:562px;top:109px;width:76px;background:#ccc"></div>
  <div class="tile" style="left:81px;top:146px;width:309px;height:307px;background:linear-gradient(135deg,#8a8a8a,#4a4a4a)" role="img" aria-label="Video of a trainer guiding a kettlebell push-up">
    <div class="abs video-controls">
      <svg width="309" height="30"><path d="M14 9l9 6-9 6z" fill="#fff"/><rect x="40" y="13" width="14" height="4" fill="#ccc"/><rect x="70" y="13" width="200" height="4" rx="2" fill="#555"/><rect x="70" y="13" width="90" height="4" rx="2" fill="#3a8fd6"/></svg>
    </div>
  </div>
  <div class="tile" style="left:404px;top:146px;width:196px;height:138px;background:linear-gradient(135deg,#777,#bbb)" role="img" aria-label="Athlete doing a kettlebell plank row"></div>
  <div class="tile" style="left:404px;top:305px;width:196px;height:148px;background:linear-gradient(160deg,#cfd8c8,#6f9a4a)" role="img" aria-label="Outdoor bootcamp group planking on grass"></div>
  <div class="tile" style="left:614px;top:146px;width:288px;height:125px;background:linear-gradient(135deg,#e8e8e8,#9a9a9a)" role="img" aria-label="Group doing push-ups in a bright studio"></div>
  <div class="tile" style="left:614px;top:284px;width:147px;height:169px;background:linear-gradient(160deg,#d8d2cc,#8a5a5a)" role="img" aria-label="Woman posing with dumbbells"></div>
  <div class="tile" style="left:775px;top:284px;width:127px;height:169px;background:linear-gradient(160deg,#9aa5a8,#4f5a5e)" role="img" aria-label="Trainer spotting a client on a balance ball"></div>
  <div class="tile" style="left:916px;top:146px;width:203px;height:307px;background:linear-gradient(160deg,#c9c9c9,#6a5e56)" role="img" aria-label="Trainer spotting a dumbbell press"></div>
  <svg class="arrow" style="left:30px;top:276px" width="18" height="36"><path d="M16 2L3 18l13 16" stroke="#fff" stroke-width="2" fill="none"/></svg>
  <svg class="arrow" style="left:1152px;top:276px" width="18" height="36"><path d="M2 2l13 16L2 34" stroke="#fff" stroke-width="2" fill="none"/></svg>
</section>

<section class="section events" role="img" aria-label="Group fitness class background, darkened">
  <h2 class="abs center title" style="top:42px">UPCOMING <b>EVENTS</b></h2>
  <div class="abs rule" style="left:347px;top:94px;width:506px"></div>
  <div class="abs center kicker" style="top:128px">JOIN US FOR AN EVENT!</div>
  <article class="event" style="left:81px">
    <div class="event-photo" style="background:linear-gradient(160deg,#9fb8d0,#6f9a4a)" role="img" aria-label="Outdoor group workout on a field"></div>
    <div class="date"><strong>12</strong><small>MAY</small></div>
    <h3>LOREM IPSUM DOLOR SIT AMET</h3>
    <p>Lorem ipsum dolor sit amet, consectetuer adipiscing elit, sed di nonummy nibh euismod tincidun euismod...</p>
    <span class="pill">READ MORE</span>
  </article>
  <article class="event" style="left:436px">
    <div class="event-photo" style="background:linear-gradient(160deg,#e6e6e6,#9a9a9a)" role="img" aria-label="Kettlebell class in a gym"></div>
    <div class="date"><strong>11</strong><small>MAY</small></div>
    <h3>LOREM IPSUM DOLOR SIT AMET</h3>
    <p>Lorem ipsum dolor sit amet, consectetuer adipiscing elit, sed di nonummy nibh euismod tincidun euismod...</p>
    <span class="pill">READ MORE</span>
  </article>
  <article class="event" style="left:792px">
    <div class="event-photo" style="background:linear-gradient(160deg,#bfd4e6,#4f7ea8)" role="img" aria-label="Suspension strap training session"></div>
    <div class="date"><strong>09</strong><small>MAY</small></div>
    <h3>LOREM IPSUM DOLOR SIT AMET</h3>
    <p>Lorem ipsum dolor sit amet, consectetuer adipiscing elit, sed di nonummy nibh euismod tincidun euismod...</p>
    <span class="pill">READ MORE</span>
  </article>
  <svg class="arrow" style="left:30px;top:281px" width="18" height="36"><path d="M16 2L3 18l13 16" stroke="#fff" stroke-width="2" fill="none"/></svg>
  <svg class="arrow" style="left:1152px;top:281px" width="18" height="36"><path d="M2 2l13 16L2 34" stroke="#fff" stroke-width="2" fill="none"/></svg>
</section>

<section class="section testimonials">
  <h2 class="abs center title" style="top:48px">CLIENT <b>TESTIMONIALS</b></h2>
  <div class="abs rule" style="left:400px;top:104px;width:400px;background:#555"></div>
  <blockquote class="abs quote">Ut wisi enim adi minim veniam, quis nostrud exerci tation more ullamcorper suscipit lobortis nis ut aliquip commodo conseqti. Duis autem iriure dolor in hendrerit in vulputate veesseml molestie consequat, vel illum facilisi. Lorem ipsum dolor sit amet, conse ctetuer adipiscing elit, sedmoi di nonummy nibh more euismod tincidunt ut laoreet dolore magna aliquam erat volutpat. Ut wisi enim admin veniam, quis nostrud exerci tation ullamco orper suscipit lobortis eamopk commodo consequat.</blockquote>
  <svg class="abs" style="left:232px;top:306px" width="40" height="34"><path d="M0 0h40L0 34z" fill="#333"/></svg>
  <div class="abs quote-name">DANE CORWELL</div>
  <svg class="arrow" style="left:30px;top:233px" width="18" height="36"><path d="M16 2L3 18l13 16" stroke="#fff" stroke-width="2" fill="none"/></svg>
  <svg class="arrow" style="left:1152px;top:233px" width="18" height="36"><path d="M2 2l13 16L2 34" stroke="#fff" stroke-width="2" fill="none"/></svg>
</section>

<footer class="section footer">
  <div class="abs newsletter">
    <svg width="26" height="22" viewBox="0 0 26 22"><rect x="1" y="3" width="24" height="17" fill="none" stroke="#aaa" stroke-width="2"/><path d="M1 3l12 9 12-9" fill="none" stroke="#aaa" stroke-width="2"/></svg>
    <span class="label">NEWSLETTER SIGNUP</span>
    <span class="input">Enter your email here</span>
    <span class="btn">SUBSCRIBE</span>
  </div>
  <div class="abs follow">FOLLOW US <span class="icon-dot" style="background:#2c4a85"></span><span class="icon-dot light"></span></div>

  <div class="abs ftitle" style="left:81px;top:164px"><span class="icon-dot light" style="width:24px;height:24px"></span>QUICK INQUIRY</div>
  <div class="field" style="left:81px;top:233px;width:226px">Name</div>
  <div class="field" style="left:81px;top:291px;width:226px">Email Address</div>
  <div class="field" style="left:81px;top:349px;width:226px">Phone Number</div>
  <div class="field" style="left:323px;top:233px;width:231px;height:98px">Message</div>
  <div class="submit" style="left:323px;top:349px;width:231px">SUBMIT</div>

  <div class="vline" style="left:605px;top:160px;height:270px"></div>
  <div class="abs ftitle" style="left:628px;top:168px"><svg width="20" height="22"><rect x="2" y="2" width="16" height="18" fill="none" stroke="#aaa" stroke-width="2"/><path d="M6 8h8M6 12h8M6 16h8" stroke="#aaa" stroke-width="2"/></svg>QUICK LINKS</div>
  <ul class="abs links" style="left:628px;top:214px">
    <li>HOME</li><li>ABOUT</li><li>SERVICES</li><li>BLOG</li><li>VIDEOS</li><li>PROGRAMS</li><li>CONTACT</li>
  </ul>

  <div class="vline" style="left:835px;top:160px;height:270px"></div>
  <div class="abs ftitle" style="left:870px;top:168px"><span class="icon-dot light" style="width:24px;height:24px"></span>CONTACT DETAILS</div>
  <div class="abs" style="left:865px;top:228px;display:flex;align-items:center;gap:12px;font-size:17px">
    <svg width="32" height="32" viewBox="0 0 28 28"><circle cx="14" cy="14" r="13" fill="none" stroke="#fff" stroke-width="2"/><path d="M9 7l4 4-2 2c1 2 3 4 5 5l2-2 4 4-2 3C13 22 6 15 6 9z" fill="#fff"/></svg>123-456-7890
  </div>
  <div class="abs" style="left:865px;top:276px;display:flex;align-items:center;gap:12px;font-size:14px">
    <svg width="32" height="32" viewBox="0 0 28 28"><circle cx="14" cy="14" r="13" fill="none" stroke="#fff" stroke-width="2"/><rect x="8" y="9" width="12" height="10" fill="none" stroke="#fff" stroke-width="1.6"/><path d="M8 9l6 5 6-5" fill="none" stroke="#fff" stroke-width="1.6"/></svg>info@vorelan.com
  </div>
  <div class="abs" style="left:865px;top:345px;width:90px;text-align:center">
    <span style="display:block;width:50px;height:50px;border-radius:50%;background:#fff;margin:0 auto 6px"></span>
    <span style="font-weight:900;font-size:22px;color:#fff">VORELAN</span>
  </div>
</footer>

<div class="section copyright">
  <svg class="abs" style="left:585px;top:-16px" width="30" height="14"><path d="M0 14L8 2h14l8 12z" fill="#777"/><path d="M10 10l5-4 5 4" stroke="#333" stroke-width="2" fill="none"/></svg>
  COPYRIGHT 2016 VORELAN | ALL RIGHT RESERVED.
</div>

</body>
</html>
```